A New and modern Business Card for Tarwick Trade Solutions Ltd

New and modern Logo and Business Card Attached is the current logo/business card designCurrently the business is called "Tarwick & Co." or TTS Ltd for short. This is subject to change.This business specialises in Telecoms and Energy. We work with the major networks (QV, K7, etc) and also offer Energy Products saving clients money off their energy bills.These are business to business services.The current design incorporates a Pheonix, indicating rebirth, starting something new.We would like to maintain the Phoenix element but a newer modern style.We love colours in the logo 3 max.The aim of this is to be ultra slick and modern. I envisage Tarwick & Co. on one side of the card with long descriptions on the other side.Side 1:TTS Ltd/Logo?Side 2:TTS Ltd/Logo/Graphic?Brogan & Co.Name:Address:Phone:Email:The design is mostly flexible but must incorporate a Phoenix.For example "Tarwick & Co." with a block phoenix behind the text...up to you.

Industry/Entity Type

Telecommunications

Contact Information for Business Card

Tarwick & Co.
Address:
Name:
Phone:
Email:

Logo Text

Tarwick & Co.

Colors
33a6d7
0792cd
acd037
9bcb3c
f78f20
fece3e

Requirements
Must have
• Phoenix
• 3/4 colours max
• Blue representing Technology (wireless)
• Green for Eco Energy
• Orange for Phoenix
• White business card background
Should not have
• phoenix must not all be red/ orange fire, we are a technology service company and the phoenix colours must represent this. Fire is not representative of our company.

```html
<!DOCTYPE html>
<html lang="en">
<head>
<meta charset="utf-8">
<title>Tarwick Trade Solutions Ltd – Business Card</title>
<link rel="stylesheet" href="https://fonts.googleapis.com/css2?family=Cinzel:wght@500;600&family=Lato:wght@400&display=swap">
<style>
  :root {
    --page-bg: #e9edf0;
    --card-bg: #ffffff;
    --card-edge: #d6dde2;
    --tech-blue: #0792cd;
    --sky-blue: #33a6d7;
    --eco-green: #9bcb3c;
    --phoenix-orange: #f78f20;
    --text-dark: #2b3238;
    --text-soft: #5b6670;
    --decor-from: #eef7fb;
    --decor-to: #f5faec;
  }
  * { box-sizing: border-box; margin: 0; padding: 0; }
  html, body {
    width: 1200px; height: 900px; overflow: hidden;
    background: var(--page-bg);
  }
  .canvas { position: relative; width: 1200px; height: 900px; }

  .card {
    position: absolute; left: 280px;
    width: 640px; height: 366px;
    background: var(--card-bg);
    border: 1px solid var(--card-edge);
    border-radius: 22px;
    overflow: hidden;
    box-shadow: 0 6px 20px rgba(30, 50, 70, 0.10);
  }
  .card--back { top: 56px; }
  .card--front { top: 478px; }

  /* back side */
  .back-mark {
    position: absolute; inset: 0;
    display: flex; align-items: center; justify-content: center; gap: 18px;
  }
  .back-mark__dot {
    width: 44px; height: 44px; border-radius: 50%;
    background: var(--phoenix-orange);
    flex: none;
  }
  .back-mark__name {
    font-family: "Cinzel", serif; font-weight: 600;
    font-size: 32px; letter-spacing: 1px;
    color: var(--tech-blue);
    white-space: nowrap;
  }
  .back-band {
    position: absolute; left: 0; right: 0; bottom: 0; height: 10px;
    background: linear-gradient(90deg, var(--tech-blue), var(--sky-blue) 50%, var(--eco-green));
  }

  /* front side */
  .front-decor {
    position: absolute; left: 0; top: 0;
    width: 250px; height: 230px;
    border-bottom-right-radius: 140px;
    background: linear-gradient(135deg, var(--decor-from), var(--decor-to));
  }
  .brand {
    position: absolute; right: 34px; top: 58px;
    display: flex; align-items: center; gap: 12px;
  }
  .brand__dot {
    width: 26px; height: 26px; border-radius: 50%;
    background: var(--phoenix-orange);
    flex: none;
  }
  .brand__name {
    font-family: "Cinzel", serif; font-weight: 600;
    font-size: 21px; color: var(--tech-blue);
    white-space: nowrap;
  }
  .rule { position: absolute; height: 1px; background: var(--eco-green); }
  .rule--top { right: 34px; top: 124px; width: 300px; }
  .rule--bottom { left: 246px; top: 262px; width: 234px; }

  .address {
    position: absolute; right: 34px; top: 150px;
    text-align: right; font-style: normal;
    font-family: "Lato", sans-serif; font-size: 17px; line-height: 1.4;
    color: var(--text-dark);
  }
  .person { position: absolute; left: 40px; top: 246px; }
  .person__name {
    font-family: "Cinzel", serif; font-weight: 600;
    font-size: 20px; letter-spacing: 0.5px;
    color: var(--phoenix-orange);
    white-space: nowrap;
  }
  .person__role {
    font-family: "Lato", sans-serif; font-size: 16px;
    color: var(--text-soft); margin-top: 2px;
  }
  .contact {
    position: absolute; left: 40px; top: 306px;
    list-style: none;
    font-family: "Lato", sans-serif; font-size: 17px;
    color: var(--text-dark);
  }
  .contact__item { display: flex; align-items: center; gap: 8px; line-height: 1.45; }
  .contact__icon { width: 16px; height: 14px; flex: none; }
</style>
</head>
<body>
<main class="canvas">
  <section class="card card--back" aria-label="Card back">
    <div class="back-mark">
      <span class="back-mark__dot"></span>
      <span class="back-mark__name">Tarwick Trade Solutions</span>
    </div>
    <div class="back-band"></div>
  </section>

  <section class="card card--front" aria-label="Card front">
    <div class="front-decor" role="img" aria-label="Faint large phoenix decoration"></div>

    <div class="brand">
      <span class="brand__dot"></span>
      <span class="brand__name">Tarwick Trade Solutions Ltd</span>
    </div>
    <div class="rule rule--top"></div>

    <address class="address">
      421, Address line here<br>
      Country Name, 45452
    </address>

    <div class="person">
      <p class="person__name">Daniel Hartley</p>
      <p class="person__role">Managing Director</p>
    </div>
    <div class="rule rule--bottom"></div>

    <ul class="contact">
      <li class="contact__item">
        <svg class="contact__icon" viewBox="0 0 16 14" aria-hidden="true">
          <path d="M1 4 Q8 -1 15 4 L13 6 L11 4.5 L5 4.5 L3 6 Z" fill="var(--tech-blue)"/>
          <rect x="3" y="6.5" width="10" height="7" rx="1.5" fill="var(--tech-blue)"/>
        </svg>
        044-987 650 213
      </li>
      <li class="contact__item">
        <svg class="contact__icon" viewBox="0 0 16 14" aria-hidden="true">
          <rect x="0.5" y="2" width="15" height="11" rx="1" fill="var(--tech-blue)"/>
          <path d="M1 3 L8 8.5 L15 3" fill="none" stroke="var(--card-bg)" stroke-width="1.3"/>
        </svg>
        info@tarwicktrade.com
      </li>
    </ul>
  </section>
</main>
</body>
</html>
```